New Word Template Design Project

I need this document for death certificate ordering to look like our branding. I will attach the pdf with the information and a sample pdf of our style. I also think that check boxes and x's would be better than yes and no.

2nd page in spanish.

Industry/Entity Type

Funeral

Requirements
Should not have
• Check boxes and red x's or yellow next to the yes, no , or sometimes

```html
<!DOCTYPE html>
<html lang="en">
<head>
<meta charset="utf-8">
<title>Death Certificate Ordering Guide – Miami-Dade County</title>
<link href="https://fonts.googleapis.com/css2?family=Jost:wght@300;400;500;600;700&display=swap" rel="stylesheet">
<style>
:root{
  --slate:#4a6b87;
  --ink:#2b2b2b;
  --muted:#3a3a3a;
  --stripe:#f2f2f2;
  --rule:#b9b9b9;
  --green:#3fae3f;
  --red:#e0261b;
  --white:#ffffff;
}
*{box-sizing:border-box;margin:0;padding:0}
html,body{width:848px;height:1200px;overflow:hidden;background:var(--white)}
body{font-family:'Jost',sans-serif;color:var(--ink);position:relative}
.brand{position:absolute;left:22px;top:50px;width:212px;display:flex;align-items:center;gap:8px}
.brand-dot{width:12px;height:12px;border-radius:50%;background:var(--slate);flex:none}
.brand-name{font-weight:500;font-size:19px;line-height:1.15;color:var(--slate)}
.header-rule{position:absolute;left:251px;top:27px;width:2px;height:109px;background:var(--slate)}
.title{position:absolute;left:286px;top:27px;font-size:33px;font-weight:500;color:var(--ink);letter-spacing:-.4px;white-space:nowrap}
.title strong{font-weight:700;color:var(--slate)}
.subtitle{position:absolute;left:286px;top:82px;font-size:29px;font-weight:300;color:var(--muted)}
.intro{position:absolute;left:22px;top:142px;width:792px;font-size:13.6px;font-weight:300;line-height:21.5px}
.table{position:absolute;left:22px;top:214px;width:804px;height:539px;border:1px solid var(--rule);border-top:none}
.thead{height:41px;background:var(--slate);color:var(--white);font-size:14px;font-weight:400;display:grid;grid-template-columns:380px 156px 134px 135px;align-items:center;margin:0 -1px}
.thead span:nth-child(1){padding-left:18px}
.thead span:nth-child(2){padding-left:2px}
.thead span:nth-child(3){padding-left:9px}
.thead span:nth-child(4){padding-left:6px}
.tbody{padding-top:8px}
.row{height:32px;display:grid;grid-template-columns:379px 156px 134px 135px;align-items:center;font-size:12.3px;font-weight:300;position:relative}
.row:nth-child(even)::before{content:"";position:absolute;left:-12px;right:-12px;top:0;bottom:0;background:var(--stripe);z-index:-1}
.row span:first-child{padding-left:17px}
.row .mark{display:flex;align-items:center;gap:6px;padding-left:25px}
.row .mark svg{width:13px;height:13px;flex:none}
.row .qty{text-align:center;padding-left:6px}
.pricing-head{position:absolute;left:20px;top:770px;font-size:17px;font-weight:500;color:var(--slate)}
.copy{position:absolute;left:22px;width:792px;font-size:13.6px;font-weight:300;line-height:21px}
.copy b{font-weight:600}
.order-q{position:absolute;left:20px;top:1004px;font-size:15.5px;font-weight:500;color:var(--slate);line-height:29px}
.order-lines{position:absolute;left:270px;top:1006px;font-size:12.5px;font-weight:300;line-height:29px}
.order-lines div{display:flex;align-items:center;gap:2px}
.order-lines svg{width:13px;height:13px;margin-right:6px}
.blank{display:inline-block;width:69px;border-bottom:1px solid var(--ink);height:12px;margin-right:2px}
.help{position:absolute;left:20px;top:1077px;font-size:15.5px;font-weight:500;color:var(--slate)}
.phone{position:absolute;left:268px;top:1073px;display:flex;align-items:center;gap:6px;font-size:19px;font-weight:700;color:var(--slate)}
.phone svg{width:13px;height:13px}
.emails{position:absolute;left:22px;top:1113px;width:800px;display:flex;justify-content:space-between;font-size:13.5px;font-weight:300}
.emails span{display:flex;align-items:center;gap:7px}
.emails svg{width:11px;height:8px}
.footer{position:absolute;left:0;top:1148px;width:848px;height:52px;background:var(--slate);color:var(--white);font-size:12px;font-weight:300}
.footer .tag{position:absolute;left:0;right:0;top:18px;text-align:center}
.footer .code{position:absolute;right:22px;top:17px;font-size:13px}
</style>
</head>
<body>
<svg width="0" height="0" style="position:absolute">
  <defs>
    <symbol id="tick" viewBox="0 0 16 16"><rect width="16" height="16" rx="3" fill="#3fae3f"/><path d="M3.8 8.3l2.9 2.9 5.5-6" fill="none" stroke="#fff" stroke-width="2.2" stroke-linecap="round" stroke-linejoin="round"/></symbol>
    <symbol id="cross" viewBox="0 0 16 16"><path d="M2.5 2.5l11 11M13.5 2.5l-11 11" stroke="#e0261b" stroke-width="2.8" stroke-linecap="round"/></symbol>
    <symbol id="mail" viewBox="0 0 12 9"><rect width="12" height="9" rx="1" fill="#4a6b87"/><path d="M.5 .8L6 5l5.5-4.2" fill="none" stroke="#fff" stroke-width="1"/></symbol>
  </defs>
</svg>

<div class="brand"><span class="brand-dot"></span><span class="brand-name">Lindhaven Funeral &amp; Cremation</span></div>
<div class="header-rule"></div>
<h1 class="title"><strong>Death Certificate</strong> Ordering Guide</h1>
<p class="subtitle">Miami-Dade County</p>

<p class="intro">Certified death certificates are used to handle legal, financial, and personal matters after a loved one passes. While some institutions require an original, others may only need to view or copy it. In Florida, you can order death certificates with or without the cause of death. Cause of death is confidential and should only be included when necessary.</p>

<div class="table">
  <div class="thead"><span>Use</span><span>Original Needed?</span><span>With Cause?</span><span>Suggested Quantity</span></div>
  <div class="tbody">
    <div class="row"><span>Life Insurance Claims</span><span class="mark"><svg><use href="#tick"/></svg>Yes</span><span class="mark"><svg><use href="#tick"/></svg>Yes</span><span class="qty">1 Per Policy</span></div>
    <div class="row"><span>Pension or Retirement Benefits</span><span class="mark"><svg><use href="#tick"/></svg>Yes</span><span class="mark"><svg><use href="#tick"/></svg>Yes</span><span class="qty">1</span></div>
    <div class="row"><span>Bank Accounts</span><span class="mark"><svg><use href="#cross"/></svg>Usually Not</span><span class="mark"><svg><use href="#cross"/></svg>No</span><span class="qty">0-1</span></div>
    <div class="row"><span>Investment / Brokerage Accounts</span><span class="mark"><svg><use href="#tick"/></svg>Sometimes</span><span class="mark"><svg><use href="#tick"/></svg>Sometimes</span><span class="qty">1-2</span></div>
    <div class="row"><span>Vehicle Title Transfer (DMV)</span><span class="mark"><svg><use href="#tick"/></svg>Yes</span><span class="mark"><svg><use href="#tick"/></svg>No</span><span class="qty">1</span></div>
    <div class="row"><span>Property / Real Estate Transfers</span><span class="mark"><svg><use href="#tick"/></svg>Yes</span><span class="mark"><svg><use href="#cross"/></svg>No</span><span class="qty">1 Per Property</span></div>
    <div class="row"><span>Probate / Court Matters</span><span class="mark"><svg><use href="#tick"/></svg>Yes</span><span class="mark"><svg><use href="#tick"/></svg>Often</span><span class="qty">1-2</span></div>
    <div class="row"><span>Social Security / Government Benefits</span><span class="mark"><svg><use href="#cross"/></svg>No</span><span class="mark"><svg><use href="#cross"/></svg>No</span><span class="qty">0</span></div>
    <div class="row"><span>Passport Cancellation / Consulates</span><span class="mark"><svg><use href="#tick"/></svg>Yes</span><span class="mark"><svg><use href="#tick"/></svg>Yes</span><span class="qty">1</span></div>
    <div class="row"><span>Domestic Travel with Cremated Remains</span><span class="mark"><svg><use href="#tick"/></svg>Yes</span><span class="mark"><svg><use href="#cross"/></svg>No</span><span class="qty">1</span></div>
    <div class="row"><span>International Travel with Cremated Remains</span><span class="mark"><svg><use href="#tick"/></svg>Yes</span><span class="mark"><svg><use href="#tick"/></svg>Sometimes</span><span class="qty">1</span></div>
    <div class="row"><span>Domestic Forwarding of Remains</span><span class="mark"><svg><use href="#tick"/></svg>Yes</span><span class="mark"><svg><use href="#cross"/></svg>No</span><span class="qty">1</span></div>
    <div class="row"><span>International Forwarding of Remains</span><span class="mark"><svg><use href="#tick"/></svg>Yes</span><span class="mark"><svg><use href="#tick"/></svg>Yes</span><span class="qty">1</span></div>
    <div class="row"><span>Credit Cards / Utility Companies</span><span class="mark"><svg><use href="#cross"/></svg>Usually Not</span><span class="mark"><svg><use href="#cross"/></svg>No</span><span class="qty">0</span></div>
    <div class="row"><span>Personal Copy / Peace of Mind</span><span class="mark"><svg><use href="#cross"/></svg>Optional</span><span class="mark"><svg><use href="#cross"/></svg>Optional</span><span class="qty">1</span></div>
  </div>
</div>

<h2 class="pricing-head">Pricing (Miami-Dade County):</h2>
<p class="copy" style="top:802px;font-size:14.5px">The first certified death certificate is <b>$20</b>, and each additional copy is <b>$16.</b></p>
<p class="copy" style="top:830px">If you are <b>traveling domestically</b> or <b>internationally with cremated remains,</b> at least one certified copy is typically required. Some countries may require the certificate <b>with cause of death.</b> We will reach out to the consulate of the destination country to confirm the specific requirements for transporting cremated remains.</p>
<p class="copy" style="top:900px">Please note: <b>Other counties may have different pricing</b> for death certificates. We will inform you of the exact cost based on the location of death.</p>
<p class="copy" style="top:948px"><b>Most families order 4 to 8 certified copies.</b> A mix is common — for example, 2 with cause and 4 without cause. It simpler and more <span style="white-space:nowrap">cost-effective</span> to order them at the time of need. If you're unsure, we are here to guide you through the process</p>

<p class="order-q">How many certified copies would<br>you like to order?</p>
<div class="order-lines">
  <div><svg><use href="#tick"/></svg><span class="blank"></span>With Cause of Death</div>
  <div><svg><use href="#tick"/></svg><span class="blank"></span>Without Cause of Death</div>
</div>

<p class="help">Questions? We’re Here for You</p>
<div class="phone"><svg viewBox="0 0 16 16"><path d="M3.2 1.5l2.6 2.6-1.4 2a9 9 0 0 0 5.5 5.5l2-1.4 2.6 2.6-1.8 1.8C7.5 14.6 1.4 8.5 1.4 3.3z" fill="#3fae3f"/></svg>(305) 555-0148</div>
<div class="emails">
  <span><svg><use href="#mail"/></svg>kendall@lindhaven.com</span>
  <span><svg><use href="#mail"/></svg>midtown@lindhaven.com</span>
  <span><svg><use href="#mail"/></svg>coralgables@lindhaven.com</span>
  <span><svg><use href="#mail"/></svg>preplanning@lindhaven.com</span>
</div>

<footer class="footer"><span class="tag">Serving Miami-Dade County with care, dignity, and support for over 100 years.</span><span class="code">C44</span></footer>
</body>
</html>
```